New letter head for Air Conditioning business

We need a new professional letter head design to suit our new re-branded air conditioning business. Our new logo is attached

```html
<!DOCTYPE html>
<html lang="en">
<head>
<meta charset="utf-8">
<title>Norvale Letterhead</title>
<link rel="stylesheet" href="https://fonts.googleapis.com/css2?family=Open+Sans:wght@400;600&family=Lato:wght@400&display=swap">
<style>
  :root {
    --ink-dark: #3d3d3f;
    --brand-green: #5fc084;
    --brand-coral: #ef6a5e;
    --body-text: #4a4a4a;
    --paper: #ffffff;
  }
  html, body { margin: 0; padding: 0; overflow: hidden; }
  body { width: 1040px; height: 1200px; background: var(--paper); }
  .letterhead {
    position: relative; width: 1040px; height: 1200px; overflow: hidden;
    background: var(--paper); color: var(--body-text);
    font-family: "Open Sans", Arial, sans-serif;
  }
  .header-wave { position: absolute; left: 0; top: 0; width: 1040px; height: 180px; }
  .brand {
    position: absolute; left: 440px; top: 72px;
    display: flex; align-items: center; gap: 16px;
  }
  .brand-dot { width: 26px; height: 26px; border-radius: 50%; background: var(--brand-green); }
  .brand-name {
    font-family: "Open Sans", Arial, sans-serif; font-weight: 600;
    font-size: 46px; letter-spacing: 4px; color: var(--ink-dark); line-height: 1;
  }
  .block { position: absolute; left: 98px; font-size: 16px; }
  .issue-date { top: 233px; }
  .recipient { top: 270px; line-height: 19px; }
  .salutation { top: 373px; }
  .letter-body {
    top: 424px; width: 840px; text-align: justify; hyphens: auto;
    line-height: 28px; font-size: 16px;
  }
  .letter-body p { margin: 0 0 26px; }
  .closing { top: 832px; }
  .signature-mark {
    position: absolute; left: 98px; top: 868px; width: 240px; height: 34px;
    background: linear-gradient(90deg, rgba(90,90,90,0.18), rgba(90,90,90,0.06));
    border-radius: 4px;
  }
  .signer-name { top: 910px; font-size: 20px; color: #333; }
  .signer-title { top: 944px; }
  .edge-tab { position: absolute; left: 0; top: 1055px; width: 21px; height: 67px; background: var(--ink-dark); }
  .contact-list {
    position: absolute; left: 98px; top: 1058px; margin: 0; padding: 0; list-style: none;
    font-family: "Lato", Arial, sans-serif; font-size: 18px; color: #222; line-height: 22px;
  }
  .contact-list li { display: flex; align-items: center; gap: 10px; }
  .contact-list svg { width: 16px; height: 16px; fill: #222; }
  .address-band {
    position: absolute; left: 0; bottom: 0; width: 1040px; height: 42px;
    background: var(--brand-coral); color: #fff; text-align: center;
    font-family: "Lato", Arial, sans-serif; font-size: 18px; line-height: 42px;
  }
</style>
</head>
<body>
<main class="letterhead">
  <svg class="header-wave" viewBox="0 0 1040 180" aria-hidden="true">
    <rect width="1040" height="180" fill="var(--ink-dark)"/>
    <path d="M0,116 C120,40 230,12 330,12 C560,12 860,84 1040,118 L1040,180 L0,180 Z" fill="var(--brand-green)"/>
    <path d="M0,136 C120,56 230,26 330,26 C560,26 860,104 1040,142 L1040,180 L0,180 Z" fill="var(--paper)"/>
  </svg>

  <div class="brand">
    <span class="brand-dot"></span>
    <span class="brand-name">NORVALE</span>
  </div>

  <div class="block issue-date">Issuing Date: May 5, 2018</div>
  <div class="block recipient">
    Name Of Employee Mr. XYZABC<br>
    Address of Employee<br>
    Address Line 2 etc..
  </div>
  <div class="block salutation">Dear Mr.XYZABC</div>

  <div class="block letter-body">
    <p>Lorem Ipsum has been the industry's standard dummy text ever since the 1500s, when an unknown printer took a galley of type and scrambled it to make a type specimen book. It has survived not only five centuries, but also the leap into electronic typesetting, remaining essentially unchanged. It was popularised in the 1960s with the release of Letraset sheets containing Lorem Ipsum passages, and more recently with desktop publishing software like Aldus PageMaker including versions of Lorem Ipsum.</p>
    <p>Lorem Ipsum is simply dummy text of the printing and typesetting industry. Lorem Ipsum has been the industry's standard dummy text ever since the 1500s, when an unknown printer took a galley of type and scrambled it to make a type specimen book.</p>
    <p>It has survived not only five centuries, but also the leap into electronic typesetting, remaining essentially unchanged. It was popularised in the 1960s with the release of Letraset sheets containing Lorem Ipsum passages.</p>
  </div>

  <div class="block closing">Yours Sincerely</div>
  <div class="signature-mark" role="img" aria-label="Handwritten signature of the managing director"></div>
  <div class="block signer-name">Marcus Hale</div>
  <div class="block signer-title">Managing Director</div>

  <div class="edge-tab"></div>
  <ul class="contact-list">
    <li><svg viewBox="0 0 16 16" aria-hidden="true"><path d="M3 2h3l1.5 3.5-2 1.2a8 8 0 0 0 3.8 3.8l1.2-2L14 10v3a1 1 0 0 1-1 1A11 11 0 0 1 2 3a1 1 0 0 1 1-1z"/></svg>044-555 0192 300</li>
    <li><svg viewBox="0 0 16 16" aria-hidden="true"><path d="M1 3h14v10H1z M2.5 4.5 8 9l5.5-4.5" fill="none" stroke="#222" stroke-width="1.5"/></svg>info@norvalecooling.com</li>
    <li><svg viewBox="0 0 16 16" aria-hidden="true"><circle cx="8" cy="8" r="6.5" fill="none" stroke="#222" stroke-width="1.5"/><path d="M1.5 8h13M8 1.5c-3 3.5-3 9.5 0 13M8 1.5c3 3.5 3 9.5 0 13" fill="none" stroke="#222" stroke-width="1.2"/></svg>www.norvalecooling.com</li>
  </ul>

  <footer class="address-band">421, Address line goes here Country Name, 45452</footer>
</main>
</body>
</html>
```